Corvane Paintless Dent Removal

Our company works on vehicles removing dents using a highly skilled trade which the metal is massaged out with special tools without disturbing the original paint, hence paintless dent removal. Besides keeping the paint and metal original its also very environmentally friendly since no paint or toxic fillers are used. Also we we are one of the most experienced companies in the business with 25 years

Target Market(s)

Retail Automobile consumers, Auto Dealerships and Auto Body Shops

Industry/Entity Type

Auto Repair

Contact Information for Business Card

Dale Hollister
PO Box 518 Brookmere, NY 11962
631-555-0148
corvanepdr@mailbox-example.com
website corvanepdr.example
youtube corvane paintless dent removal
25 years of experience removing Dents, Dings and Hail Damage

Font styles to use
Serif
Sans Serif

Colors

Designer to choose colors to be used in the design.

Requirements
Must have
• I do like things that are simple but classy and somewhat bold, also I like my logo so that should be somewhat important

```html
<!DOCTYPE html>
<html lang="en">
<head>
<meta charset="utf-8">
<title>Corvane Paintless Dent Removal — Business Card</title>
<link rel="stylesheet" href="https://fonts.googleapis.com/css2?family=Roboto:wght@400;500;700&display=swap">
<style>
  :root {
    --backdrop: #6e4d36;
    --card-white: #f4f4f4;
    --navy: #122a52;
    --lime: #7dc512;
    --text-grey: #555a60;
    --divider: #c9c9c9;
    --seal-gold: #d9a92c;
    --seal-dark: #1a1a1a;
    --white: #ffffff;
  }
  * { margin: 0; padding: 0; box-sizing: border-box; }
  html, body { width: 1200px; height: 960px; overflow: hidden; }
  body {
    position: relative;
    background: var(--backdrop);
    font-family: "Roboto", Arial, sans-serif;
  }
  .card {
    position: absolute;
    width: 600px;
    height: 343px;
    overflow: hidden;
    box-shadow: 0 3px 8px rgba(0,0,0,0.45);
  }
  .card-front { left: 314px; top: 113px; background: var(--card-white); }
  .card-back { left: 311px; top: 472px; background: var(--lime); }

  .front-wave { position: absolute; left: 0; top: 0; width: 600px; height: 343px; }

  .brand-mark {
    position: absolute;
    left: 40px; top: 138px;
    display: flex; align-items: center; gap: 10px;
  }
  .brand-dot {
    width: 22px; height: 22px; border-radius: 50%;
    background: var(--lime);
    flex: none;
  }
  .brand-name {
    font-weight: 700;
    font-size: 21px;
    line-height: 1.15;
    color: var(--navy);
  }

  .seal {
    position: absolute; right: 26px; top: 29px;
    width: 70px; height: 70px; border-radius: 50%;
    background: var(--seal-gold);
    display: flex; align-items: center; justify-content: center;
  }
  .seal-core { width: 56px; height: 56px; border-radius: 50%; background: var(--seal-dark); }

  .divider {
    position: absolute; left: 308px; top: 97px;
    width: 1px; height: 152px; background: var(--divider);
  }

  .contact { position: absolute; left: 332px; top: 93px; color: var(--text-grey); }
  .contact-name {
    font-weight: 500; font-size: 20px; color: var(--navy);
    letter-spacing: 0.3px; margin-bottom: 9px;
  }
  .contact-address { font-size: 14px; line-height: 19px; margin-bottom: 6px; }
  .contact-list { list-style: none; font-size: 14px; }
  .contact-list li { display: flex; align-items: center; height: 19px; }
  .contact-list svg { width: 13px; height: 13px; margin-right: 10px; flex: none; fill: var(--navy); }

  .back-name {
    position: absolute; left: 0; right: 0; top: 148px;
    text-align: center;
    font-weight: 700; font-size: 30px; line-height: 1.15;
    color: var(--white);
  }
  .back-url {
    position: absolute; left: 0; right: 0; top: 280px;
    text-align: center;
    font-size: 13px; letter-spacing: 5px;
    color: var(--white);
  }
</style>
</head>
<body>

<section class="card card-front">
  <svg class="front-wave" viewBox="0 0 600 343" aria-hidden="true">
    <path d="M0 252 C200 286 400 312 600 314 L600 319 C400 320 200 302 0 268 Z" fill="var(--lime)"/>
    <path d="M0 274 C200 304 400 326 600 322 L600 343 L0 343 Z" fill="var(--navy)"/>
  </svg>

  <div class="brand-mark">
    <span class="brand-dot"></span>
    <div class="brand-name">Corvane<br>Paintless Dent Removal</div>
  </div>

  <div class="seal" role="img" aria-label="25 years of experience seal"><div class="seal-core"></div></div>

  <div class="divider"></div>

  <div class="contact">
    <h1 class="contact-name">DALE HOLLISTER</h1>
    <p class="contact-address">PO Box 518<br>Brookmere, NY 11962</p>
    <ul class="contact-list">
      <li><svg viewBox="0 0 24 24"><path d="M6.6 10.8a15.1 15.1 0 0 0 6.6 6.6l2.2-2.2c.3-.3.7-.4 1-.2 1.1.4 2.3.6 3.6.6.6 0 1 .4 1 1V20c0 .6-.4 1-1 1A17 17 0 0 1 3 4c0-.6.4-1 1-1h3.5c.6 0 1 .4 1 1 0 1.3.2 2.5.6 3.6.1.3 0 .7-.2 1z"/></svg>631-555-0148</li>
      <li><svg viewBox="0 0 24 24"><path d="M2 5h20v14H2z" fill="none"/><path d="M2 5h20v2l-10 6L2 7zm0 4 10 6 10-6v10H2z"/></svg>corvanepdr@mailbox-example.com</li>
      <li><svg viewBox="0 0 24 24"><path d="M12 2a10 10 0 1 0 0 20 10 10 0 0 0 0-20zm6.9 6h-3a15.7 15.7 0 0 0-1.4-3.6A8 8 0 0 1 18.9 8zM12 4c.8 1.2 1.5 2.5 1.9 4h-3.8c.4-1.5 1.1-2.8 1.9-4zM4.3 14a8 8 0 0 1 0-4h3.4a16.5 16.5 0 0 0 0 4zm.8 2h3a15.7 15.7 0 0 0 1.4 3.6A8 8 0 0 1 5.1 16zm3-8h-3a8 8 0 0 1 4.4-3.6C8.9 5.5 8.4 6.7 8.1 8zM12 20c-.8-1.2-1.5-2.5-1.9-4h3.8c-.4 1.5-1.1 2.8-1.9 4zm2.3-6H9.7a14.7 14.7 0 0 1 0-4h4.6a14.7 14.7 0 0 1 0 4zm.2 5.6c.6-1.1 1.1-2.3 1.4-3.6h3a8 8 0 0 1-4.4 3.6zm1.8-5.6a16.5 16.5 0 0 0 0-4h3.4a8 8 0 0 1 0 4z"/></svg>corvanepdr.example</li>
      <li><svg viewBox="0 0 24 24"><rect x="2" y="5" width="20" height="14" rx="3"/><path d="M10 9v6l5-3z" fill="var(--card-white)"/></svg>corvane paintless dent removal</li>
    </ul>
  </div>
</section>

<section class="card card-back">
  <div class="back-name">Corvane<br>Paintless Dent Removal</div>
  <p class="back-url">www.corvanepdr.example</p>
</section>

</body>
</html>
```